Letterhead for a German Distribution/Manufacturing Company

We need a professional Letterhead in a unique Design.
not to playful.
The Letterhead has to show show that we are a international company with headquater in Germany.
all details like adress, Vat Tax Number, Bank Accout, Eori, email, Company number has to be on the Letterhead.
for example use: VAT TAX DE5470318 Bank Account: Kestrel Bank IBAN DE412058731ß204683 Swift: MORV0417352 EORI 3150428697 Company Number: HRB 51806 Adress: VOLMINTA UG Ahornweg 7 Postal Code 06384 City Kelbrunn Country: Germany Email: info@volminta-example.com
the design can be colored but doesnt have to be
Industry/Entity Type
Manufacturing and international distribution
Requirements
Must have
- show that we are a international company with headquater in Germany. our company infos and logo

```html
<!DOCTYPE html>
<html lang="en">
<head>
<meta charset="utf-8">
<title>Volminta Letterhead</title>
<link href="https://fonts.googleapis.com/css2?family=Lato:wght@400;700&family=Dancing+Script:wght@500&display=swap" rel="stylesheet">
<style>
  :root {
    --backdrop: #e4e4e6;
    --paper: #ffffff;
    --band: #4d4d4d;
    --ink: #2b2b2b;
    --ink-light: #ffffff;
  }
  * { margin: 0; padding: 0; box-sizing: border-box; }
  html, body {
    width: 1200px; height: 874px; overflow: hidden;
    background: var(--backdrop);
    font-family: "Lato", Arial, sans-serif;
    color: var(--ink);
  }
  .letterhead {
    position: absolute; left: 310px; top: 27px;
    width: 580px; height: 820px;
    background: var(--paper);
    box-shadow: 0 6px 18px rgba(0,0,0,0.12);
    overflow: hidden;
  }
  .letterhead__header {
    height: 140px; background: var(--band); color: var(--ink-light);
    display: flex; align-items: center; padding: 0 40px;
  }
  .brand { display: flex; align-items: center; gap: 12px; }
  .brand__mark { width: 34px; height: 34px; border-radius: 50%; background: var(--ink-light); }
  .brand__name { font-size: 30px; font-weight: 400; letter-spacing: 1px; }
  .company-details {
    margin-left: 40px; padding-left: 14px;
    border-left: 1px solid var(--ink-light);
    font-size: 8.5px; line-height: 1.45; letter-spacing: 0.2px;
  }
  .letter { padding: 46px 60px 0 60px; font-size: 11.5px; line-height: 1.4; }
  .letter__date { margin-bottom: 18px; }
  .letter__recipient { margin-bottom: 14px; }
  .letter__salutation { font-weight: 700; font-size: 14px; margin-bottom: 10px; }
  .letter__body p { max-width: 430px; margin-bottom: 14px; }
  .letter__closing { margin-top: 20px; }
  .letter__signature {
    font-family: "Dancing Script", cursive; font-size: 34px;
    margin-top: 8px; margin-left: 40px;
  }
  .letterhead__footer {
    position: absolute; left: 0; bottom: 0;
    width: 100%; height: 44px;
    background: var(--band);
  }
  .letterhead__footer-rule {
    position: absolute; left: 0; bottom: 52px;
    width: 100%; height: 3px;
    background: var(--band);
  }
</style>
</head>
<body>
  <main class="letterhead">
    <header class="letterhead__header">
      <div class="brand">
        <span class="brand__mark"></span>
        <span class="brand__name">VOLMINTA</span>
      </div>
      <div class="company-details">
        VAT TAX DE5470318<br>
        Bank Account: Kestrel Bank IBAN DE412058731ß204683<br>
        Swift: MORV0417352<br>
        EORI 3150428697<br>
        Company Number: HRB 51806<br>
        Adress: VOLMINTA UG Ahornweg 7 Postal Code 06384<br>
        City Kelbrunn Country<br>
        Germany Email: info@volminta-example.com
      </div>
    </header>

    <section class="letter">
      <p class="letter__date">January-03-2020</p>
      <p class="letter__recipient">Mr, John Doe<br>President</p>
      <p class="letter__recipient">Alder Works<br>123 Street Name, Suite# 10<br>City, State, 120023</p>
      <p class="letter__salutation">Dear Mr, John</p>
      <div class="letter__body">
        <p>Lorem ipsum dolor sit amet, consectetur adipisicing elit, sed do eiusmod tempor incididunt ut labore et dolore magna aliqua. Ut enim ad minim veniam, quis nostrud exercitation ullamco laboris nisi ut aliquip ex ea commodo consequat. Duis aute irure dolor in reprehenderit in voluptate velit esse cillum dolore eu fugiat nulla pariatur.</p>
        <p>Lorem ipsum dolor sit amet, consectetur adipisicing elit, sed do eiusmod tempor incididunt ut labore et dolore magna aliqua. Ut enim ad minim veniam, quis nostrud exercitation ullamco laboris nisi ut aliquip ex ea commodo consequat. Duis aute irure dolor in reprehenderit in voluptate velit esse cillum dolore eu fugiat nulla pariatur.</p>
        <p>Lorem ipsum dolor sit amet, consectetur adipisicing elit, sed do eiusmod tempor incididunt ut labore et dolore magna aliqua. Ut enim ad minim veniam, quis nostrud exercitation ullamco laboris nisi ut aliquip ex ea commodo consequat.</p>
        <p>Excepteur sint occaecat cupidatat non proident, sunt in culpa qui officia deserunt mollit anim id est laborum. re et dolore magnam aliquam quaerat voluptatem.</p>
      </div>
      <p class="letter__closing">Regards</p>
      <p class="letter__signature">Henrik Vollmer</p>
    </section>

    <div class="letterhead__footer-rule"></div>
    <footer class="letterhead__footer"></footer>
  </main>
</body>
</html>
```